Marrowind - IT Consultancy Website

Our company is called Marrowind and our purpose is to help companies sustainably embrace and reap the benefits of cloud platforms, through transforming practices, skills and technology using DevOps and Security practices such that they are able to automate, manage and secure their cloud platforms to deliver product to market with increasing velocity.

To get our business started I require a website that will model the typical layout of an IT consultancy services company to an Australian Market. There are many examples of such a site, here are some of them. We would like a landing page and then a few simple menu options (About, Blog, Services etc..) to additional content

http://pelvo.com.au/
http://www.brisket.com.au/
http://www.tandu.com.au/

I require the site to be created with a separate CSS file that maintains the colour palette. This is a very important requirement, I want to be able to change the colours employed in the site in a single location and not have to scan through multiple files to replace the codes.

The website must be built using static content as it will not be hosted on a web server but instead in QNT using S3 and CloudFront CDN. Therefore please stick to HTML, JavaScript, CSS and other static file formats. The website needs to be response, smooth and reactive. It should render on desktop, mobile and tablet and feature smooth scrolling, transitions and fade in's.

The website should give the customer confidence that they are dealing with a highly professional IT services company, focused strongly on cloud (QNT, Vantrel Skyline, Horvik Vapor etc..), motivated by beautiful and fluid design.

In order to make this simpler for you, the designer, I have already purchased this template from https://skinmarketly.com/theme/the-venture-allround-template-KX7Q41093 and uploaded it. Feel free to use this template if you choose (note that it makes use of a separate color palette which is a key requirement) or use one of your own choosing. If you do use this template ensure that it does not look too much like "another bootstrap site" therefore use the layout and widgets but make the site look fresh and original too.
Obviously you must delete all trace of the bootstrap package once the project has completed if you do use it

Target Market(s)

Corporate and medium enterprise businesses

Industry/Entity Type

Information Technology

Coding

Coded - Design and coding required

Number of Pages Required

4 page

Font styles to use
Sans Serif

Colors
abd036
33a6d7

Requirements
Must have
• The website should give the customer confidence that they are dealing with a highly professional IT services company, focused strongly on cloud (QNT, Vantrel Skyline, Horvik Vapor etc..), motivated by beautiful and fluid design. Our company name is Marrowind, the site needs to pay homage to the themes of fluidity and logic
• Along with About Us, Services and a Blog page could I also get social logo's included too
Nice to have
• The website must be built using static content as it will not be hosted on a web server but instead in QNT using S3 and CloudFront CDN. Therefore please stick to HTML, JavaScript, CSS and other static file formats. The website needs to be response, smooth and reactive. It should render on desktop, mobile and tablet and feature smooth scrolling, transitions and fade in's.
Should not have
• Lurid colours, or too much animations. The design must "flow"

```html
<!DOCTYPE html>
<html lang="en">
<head>
<meta charset="utf-8">
<title>Marrowind – Cloud Infrastructure Security</title>
<link href="https://fonts.googleapis.com/css2?family=Roboto:wght@300;400;500;700&family=Shadows+Into+Light&display=swap" rel="stylesheet">
<style>
:root{
  --blue:#33a6d7;
  --blue-deep:#1f7fb0;
  --green:#abd036;
  --logo-green:#4fb28a;
  --navy:#1c2a44;
  --navy-light:#2a4d78;
  --pale:#dcedf5;
  --nav-bg:#e8f4f8;
  --strip:#f2f5f7;
  --ink:#222;
  --muted:#666;
  --white:#fff;
}
*{margin:0;padding:0;box-sizing:border-box}
html,body{width:816px;height:1200px;overflow:hidden}
body{font-family:'Roboto',sans-serif;color:var(--ink);position:relative;background:var(--white)}
.abs{position:absolute}

.topbar{left:0;top:0;width:816px;height:23px;background:var(--blue);color:var(--white);font-size:9.5px}
.topbar .contact{left:36px;top:6px;display:flex;gap:20px}
.topbar .social{left:618px;top:8px;display:flex;gap:18px}
.dot{width:7px;height:7px;border-radius:50%;background:var(--white);display:block}
.topbar .login{left:700px;top:6px}
.topbar .search{left:770px;top:7px;width:8px;height:8px;border:1.5px solid var(--white);border-radius:50%}

.navbar{left:0;top:23px;width:816px;height:47px;background:var(--nav-bg)}
.brand{left:32px;top:14px;display:flex;align-items:center;gap:7px;font-size:19px;font-weight:500;color:var(--logo-green)}
.brand i{width:16px;height:16px;border-radius:50%;background:var(--logo-green);display:block}
.menu{left:393px;top:18px;display:flex;gap:26px;font-size:11.5px;color:#222;letter-spacing:.2px}

.hero{left:0;top:70px;width:816px;height:373px;background:var(--navy)}
.sphere{left:15px;top:55px;width:300px;height:300px;border-radius:50%;background:radial-gradient(circle at 45% 40%,#2b5b8c,#1d3358 70%,var(--navy))}
.hero h1{font-family:'Shadows Into Light',cursive;font-weight:400;color:var(--white);font-size:50px;line-height:56px;text-align:center;left:320px;top:76px;width:490px}
.hero .sub{left:330px;top:200px;width:470px;text-align:center;color:var(--white);font-size:14.5px;font-weight:500}
.btn{top:229px;height:24px;font-size:7.5px;font-weight:700;color:var(--white);display:flex;align-items:center;justify-content:center;text-transform:uppercase;border-radius:2px}
.btn.primary{left:469px;width:64px;background:var(--blue)}
.btn.ghost{left:548px;width:73px;border:1px solid var(--white)}
.badge{left:631px;top:228px;width:51px;height:26px;background:var(--white)}

.announce{left:0;top:443px;width:816px;height:50px;background:var(--blue);color:var(--white)}
.announce .bubble{left:33px;top:17px;width:18px;height:14px;border:1.5px solid var(--white);border-radius:2px}
.announce .msg{left:102px;top:18px;font-size:11px;font-weight:500}
.announce svg{position:absolute;top:18px}

.welcome{left:0;top:493px;width:816px;height:535px;background:var(--pale)}
.welcome h2{left:0;top:18px;width:816px;text-align:center;font-size:15px;font-weight:500}
.welcome .rule{left:28px;top:44px;width:762px;border-top:1px dashed #8fb7c9}
.feature{top:74px;width:240px;text-align:center}
.feature .ic{width:51px;height:51px;background:var(--blue);margin:0 auto;display:flex;align-items:center;justify-content:center}
.feature h3{font-size:12.5px;font-weight:500;margin-top:14px}
.feature p{font-size:8.8px;color:var(--muted);margin-top:14px;line-height:13.5px;font-weight:300}

.tab{top:242px;height:30px;font-size:12.5px;font-weight:500;display:flex;align-items:center;justify-content:center;background:var(--white);color:#222}
.tab.active{background:var(--blue);color:var(--white)}

.diagram{left:38px;top:310px;width:330px;height:175px;border-radius:90px;background:radial-gradient(circle at 75% 50%,#1f6ea3 0 30%,#eaf3f7 31% 60%,var(--pale) 75%)}
.detail{left:440px;top:292px;width:272px}
.detail h4{font-size:16px;font-weight:400;color:#555}
.detail h5{font-size:11px;color:var(--blue);font-weight:500;margin-top:8px;line-height:12px}
.detail ul{list-style:none;margin-top:8px}
.detail li{font-size:8.8px;color:#555;line-height:13.5px;margin-bottom:5px;font-weight:300;padding-left:14px;position:relative}
.detail li::before{content:"";position:absolute;left:1px;top:2px;width:4px;height:7px;border:solid var(--blue);border-width:0 2px 2px 0;transform:rotate(45deg)}
.detail p{font-size:8.8px;color:#555;line-height:13.5px;margin-top:14px;font-weight:300}

.partners{left:0;top:1028px;width:816px;height:89px;background:var(--strip);display:flex;justify-content:space-around;align-items:center;padding:0 60px}
.partner{display:flex;align-items:center;gap:5px;font-size:14px;font-weight:700;color:#9aa;filter:blur(1px)}
.partner i{width:14px;height:14px;border-radius:50%;background:#9aa;display:block}

.footer{left:0;top:1117px;width:816px;height:83px;background:var(--blue);color:var(--white)}
.footer .links{left:16px;top:21px;display:flex;gap:22px;font-size:9.5px;letter-spacing:.5px}
.footer .addr{left:16px;top:44px;font-size:9px;opacity:.85}
.footer .legal{left:16px;top:66px;font-size:7.5px;display:flex;gap:12px;opacity:.85}
.footer .legal span{padding-right:12px;border-right:1px solid rgba(255,255,255,.6)}
.footer .socials{left:689px;top:13px;display:flex;gap:6px}
.footer .socials span{width:25px;height:25px;background:#eef4f7;color:#223;font-size:8px;font-weight:700;display:flex;align-items:center;justify-content:center}
.footer .copy{left:600px;top:58px;width:206px;text-align:right;font-size:8.5px;opacity:.85}
</style>
</head>
<body>

<div class="abs topbar">
  <div class="abs contact"><span>☏ +1 800 555 01 47</span><span>✉ hello@marrowind.example</span></div>
  <div class="abs social" aria-label="Social links"><span class="dot" title="Facely"></span><span class="dot" title="Chirpa"></span><span class="dot" title="Circlo"></span></div>
  <div class="abs login">→ Login</div>
  <div class="abs search"></div>
</div>

<div class="abs navbar">
  <div class="abs brand"><i></i>Marrowind</div>
  <nav class="abs menu"><span>PRODUCT</span><span>ABOUT</span><span>RESOURCES</span><span>PRICING</span><span>BLOG</span><span>CONTACT</span></nav>
</div>

<section class="abs hero">
  <div class="abs sphere" role="img" aria-label="Glowing network sphere of connected points"></div>
  <h1 class="abs">Cloud Infrastructure<br>Security for QNT</h1>
  <div class="abs sub">Security and Compliance Automation - Built For Modern IT</div>
  <a class="abs btn primary">Get Started</a>
  <a class="abs btn ghost">Go on Surfing</a>
  <div class="abs badge" role="img" aria-label="Partner badge"></div>
</section>

<div class="abs announce">
  <div class="abs bubble"></div>
  <div class="abs msg">Webinar - Security Automation for DevOps ▸</div>
  <svg style="left:748px" width="10" height="16" viewBox="0 0 10 16"><path d="M8 1 2 8l6 7" fill="none" stroke="#fff" stroke-width="1.6"/></svg>
  <svg style="left:784px" width="10" height="16" viewBox="0 0 10 16"><path d="M2 1l6 7-6 7" fill="none" stroke="#fff" stroke-width="1.6"/></svg>
</div>

<section class="abs welcome">
  <h2 class="abs">Welcome - We're Marrowind</h2>
  <div class="abs rule"></div>

  <div class="abs feature" style="left:33px">
    <div class="ic"><svg width="30" height="30" viewBox="0 0 30 30" fill="none" stroke="#fff" stroke-width="2.4"><path d="M5 13a10 10 0 0 1 18-5M25 17a10 10 0 0 1-18 5"/><path d="M23 3v5h-5M7 27v-5h5"/></svg></div>
    <h3>Complete visibility into your QNT cloud</h3>
    <p>Good cloud security is knowing where ALL your risk and vulnerabilities are – and how to fix them – continuously</p>
  </div>
  <div class="abs feature" style="left:288px">
    <div class="ic"><svg width="32" height="26" viewBox="0 0 32 26" fill="#fff"><rect x="2" y="16" width="3" height="10"/><rect x="7" y="12" width="3" height="14"/><rect x="12" y="14" width="3" height="12"/><rect x="17" y="9" width="3" height="17"/><rect x="22" y="11" width="3" height="15"/><rect x="27" y="6" width="3" height="20"/><path d="M2 10 9 5l5 3 7-6 6 3 4-4" fill="none" stroke="#fff" stroke-width="1.6"/></svg></div>
    <h3>Proactively prioritize and remediate risk</h3>
    <p>Quickly mitigate cloud vulnerabilities and misconfigurations that lead to compromise</p>
  </div>
  <div class="abs feature" style="left:542px">
    <div class="ic"><svg width="30" height="30" viewBox="0 0 30 30" fill="none" stroke="#fff" stroke-width="1.8"><circle cx="15" cy="15" r="12"/><path d="M15 7v8l-3 4"/></svg></div>
    <h3>Up and running in minutes</h3>
    <p>No agents. No configuration changes. No hassle. Marrow Guard provides complete visibility into your QNT cloud within minutes of activation</p>
  </div>

  <div class="abs tab active" style="left:222px;width:105px">For Modern IT</div>
  <div class="abs tab" style="left:338px;width:154px">For Risk &amp; Compliance</div>
  <div class="abs tab" style="left:504px;width:89px">For DevOps</div>

  <div class="abs diagram" role="img" aria-label="Integration bubbles around a DevOps cycle of develop, test, deploy to staging, security check and deploy to production"></div>

  <div class="abs detail">
    <h4>Native QNT Security for Modern IT</h4>
    <h5>Accelerate Workload Migration with Security Automation</h5>
    <ul>
      <li>Agentless, Non-intrusive Deployment in Minutes</li>
      <li>Continuously Identify Risk Across All QNT Accounts, Regions and Services</li>
      <li>Rapidly Mitigate Risk with Step-by-Step, Guided Remediation</li>
      <li>Integrates with SIEM and Other Solutions via Direct and Custom API Integration</li>
    </ul>
    <p>Lorem ipsum dolor sit amet, consectetur adipiscing elit, sed do eiusmod tempor incididunt ut labore et dolore magna aliqua. Ut enim ad minim veniam, quis nostrud exercitation ullamco laboris nisi ut aliquip ex ea commodo consequat.</p>
  </div>
</section>

<div class="abs partners">
  <span class="partner"><i></i>Quillpress</span>
  <span class="partner"><i></i>Pixalon</span>
  <span class="partner"><i></i>Postbird</span>
  <span class="partner"><i></i>Pixalon</span>
  <span class="partner"><i></i>Postbird</span>
  <span class="partner"><i></i>Quillpress</span>
</div>

<footer class="abs footer">
  <nav class="abs links"><span>PRODUCT</span><span>ABOUT</span><span>RESOURCES</span><span>PRICING</span><span>LOGIN</span></nav>
  <div class="abs addr">14 Tallow Lane, Brisbane | sales@marrowind.example | support@marrowind.example</div>
  <div class="abs legal"><span>Security</span><span>Privacy</span><span>Terms of Service</span></div>
  <div class="abs socials"><span title="Chirpa">Ch</span><span title="Facely">Fa</span><span title="Vidly">Vi</span><span title="Linkr">Lk</span></div>
  <div class="abs copy">Copyright © 2016 Marrowind All rights reserved.</div>
</footer>

</body>
</html>
```